10-year customer thank you card

We want a greeting card that our sales reps can send to companies/customers who have been with our company for 10 or more years. We're a software company, our corporate color is blue but we also like green, orange, and purple. We'd like something rather minimal/simplistic for this card, perhaps building off our tree logo. We're really open to ideas for this one. You must use the template files that are uploaded. Copy included in 10 year thank you card file; the copy may change based on how it looks when laid out
Updates

I updated our brief. We'd prefer a sans serif font. I also uploaded a blank infographic image that includes more of our approved colors.

Industry/Entity Type

Software

Font styles to use
Sans Serif

```html
<!DOCTYPE html>
<html lang="en">
<head>
<meta charset="utf-8">
<title>Larchwell Software – 10 Years Thank You Card</title>
<link rel="stylesheet" href="https://fonts.googleapis.com/css2?family=Montserrat:wght@300;500;600&family=Allura&display=swap">
<style>
  :root {
    --paper: #ffffff;
    --header-grey: #d6d6d6;
    --brand-green: #1f7a22;
    --rule-dark: #1a1a1a;
    --arc-green: #237a2b;
    --arc-forest: #21613c;
    --arc-teal: #2a5776;
    --arc-blue: #2f5096;
    --arc-bright: #1333c0;
    --ink-light: #ffffff;
  }
  * { box-sizing: border-box; margin: 0; padding: 0; }
  html, body {
    width: 879px; height: 1200px; overflow: hidden;
    background: var(--paper);
  }
  .card {
    position: relative;
    width: 879px; height: 1200px;
    background: var(--paper);
    overflow: hidden;
    font-family: "Montserrat", sans-serif;
  }
  /* Back panel header, printed upside down for the fold */
  .back-header {
    position: absolute; top: 0; left: 0;
    width: 879px; height: 78px;
    background: var(--header-grey);
    border-top: 9px solid var(--brand-green);
    border-bottom: 2px solid var(--rule-dark);
    display: flex; align-items: center; justify-content: space-between;
    padding: 0 42px;
    transform: rotate(180deg);
  }
  .back-header .brand {
    display: flex; align-items: center; gap: 8px;
    color: var(--brand-green);
    font-weight: 600; font-size: 21px;
  }
  .back-header .brand-mark {
    width: 14px; height: 14px; background: var(--brand-green);
  }
  .back-header .web {
    color: var(--brand-green);
    font-weight: 500; font-size: 18px;
  }
  /* Front panel */
  .front {
    position: absolute; left: 0; top: 607px;
    width: 879px; height: 593px;
  }
  .front .arcs {
    position: absolute; inset: 0;
    width: 879px; height: 593px; display: block;
  }
  .years {
    position: absolute; left: 636px; top: 49px;
    width: 202px; height: 64px;
    border-top: 2px solid var(--ink-light);
    border-bottom: 2px solid var(--ink-light);
    display: flex; align-items: center; justify-content: center;
    color: var(--ink-light);
    font-weight: 300; font-size: 40px; letter-spacing: 0.5px;
  }
  .brand-feature {
    position: absolute; left: 290px; top: 230px;
    width: 300px; text-align: center;
    color: var(--ink-light);
    font-weight: 600; font-size: 40px;
  }
  .thanks {
    position: absolute; left: 0; top: 420px;
    width: 879px; text-align: center;
    color: var(--ink-light);
    font-family: "Allura", cursive;
    font-size: 112px; line-height: 1;
    padding-left: 10px;
  }
</style>
</head>
<body>
  <main class="card">
    <header class="back-header">
      <div class="brand"><span class="brand-mark"></span>Larchwell Software</div>
      <div class="web">www.larchwell.com</div>
    </header>

    <section class="front">
      <svg class="arcs" viewBox="0 455 659 445" preserveAspectRatio="none" aria-hidden="true">
        <rect x="0" y="455" width="659" height="445" fill="var(--arc-green)"/>
        <circle cx="1150" cy="1200" r="1246" fill="var(--arc-forest)"/>
        <circle cx="1150" cy="1200" r="1120" fill="var(--arc-teal)"/>
        <circle cx="1000" cy="1000" r="790" fill="var(--arc-blue)"/>
        <circle cx="900" cy="1000" r="405" fill="var(--arc-bright)"/>
      </svg>
      <div class="years">10 YEARS</div>
      <div class="brand-feature">Larchwell</div>
      <div class="thanks">Thank You</div>
    </section>
  </main>
</body>
</html>
```